School Poster

Design so that these can be placed in classrooms across the school.

Attached is another design we have had done. Use a similar theme.

Consider using themes from https://corvalhs.edq.example.au/

please edit Binder1 doc.

Students and teachers

```html
<!DOCTYPE html>
<html lang="en">
<head>
<meta charset="utf-8">
<title>Classroom Posters – Corval State High</title>
<link href="https://fonts.googleapis.com/css2?family=Archivo+Black&family=Arimo:ital,wght@0,400;0,700;1,400;1,700&display=swap" rel="stylesheet">
<style>
  :root{
    --navy:#233876;
    --blue:#1f3a93;
    --yellow:#f0e449;
    --pale:#f8f5cc;
    --lilac:#e3e3f2;
    --stripe:#bfc2e1;
    --ink:#1b1b2a;
    --bg:#c8c8c8;
    --white:#ffffff;
  }
  *{box-sizing:border-box;margin:0;padding:0}
  html,body{width:1200px;height:1200px;overflow:hidden;background:var(--bg)}
  body{position:relative;font-family:"Arimo",Arial,sans-serif;color:var(--ink)}
  .poster{position:absolute;top:259px;width:484px;height:682px;background:var(--white);overflow:hidden}
  .poster--steps{left:92px}
  .poster--ai{left:628px}
  .header-bg{position:absolute;left:0;top:0;width:484px;height:150px}
  .school-mark{position:absolute;left:26px;top:14px;width:90px;text-align:center;color:var(--white);font-weight:700;font-size:10px;line-height:1.25;letter-spacing:.5px}
  .school-mark .dot{display:block;width:50px;height:50px;border-radius:50%;background:var(--white);margin:0 auto 8px}
  .kicker{position:absolute;left:129px;top:14px;color:var(--white);font-weight:700;font-size:18px;letter-spacing:.3px;white-space:nowrap}
  .headline{position:absolute;font-family:"Archivo Black",Arial,sans-serif;color:var(--yellow);text-transform:uppercase;white-space:nowrap}
  .poster--steps .headline{left:128px;top:38px;font-size:39px;line-height:40px}
  .poster--ai .headline{left:131px;top:29px;font-size:26px;line-height:35px}
  .headline .light{color:var(--white)}

  /* steps */
  .step{position:absolute;left:23px;width:438px;border:1.5px solid var(--blue);border-radius:0 8px 8px 8px;background:var(--lilac)}
  .step-tab{position:absolute;left:-1.5px;top:-18px;height:20px;padding:0 10px 0 28px;background:var(--yellow);border:1.5px solid var(--blue);border-radius:0 12px 12px 0;font-family:"Archivo Black",Arial,sans-serif;font-size:14px;line-height:17px;color:var(--blue);white-space:nowrap}
  .step-num{position:absolute;left:-1.5px;top:-1.5px;width:21px;height:20px;background:var(--blue);color:var(--white);border-radius:0 10px 10px 0;font-family:"Arimo",sans-serif;font-weight:700;font-size:13px;line-height:20px;text-align:center}
  .step-side{position:absolute;left:0;top:0;bottom:0;width:146px;background:var(--pale);border-radius:0 0 0 7px;text-align:center;color:var(--blue);font-weight:700;font-style:italic;font-size:13px;line-height:16px;display:flex;flex-direction:column;align-items:center;justify-content:center;gap:10px;padding-top:6px}
  .step-side svg{width:40px;height:40px}
  .step-list{position:absolute;left:146px;right:0;top:0;bottom:0;border-left:2px dotted var(--blue);padding-top:16px;list-style:none}
  .step-list li{height:21px;line-height:21px;font-size:13px;padding-left:26px;position:relative;white-space:nowrap}
  .step-list li::before{content:"";position:absolute;left:14px;top:8px;width:4px;height:4px;border-radius:50%;background:var(--blue)}
  .step-list li:nth-child(odd){background:var(--stripe)}
  .step-list .note{background:none!important;font-style:italic;padding-left:14px;margin-top:12px}
  .step-list .note::before{display:none}
  .step--think{top:185px;height:102px}
  .step--supports{top:317px;height:143px}
  .step--ask{top:491px;height:121px}
  .motto{position:absolute;left:84px;top:649px;width:314px;height:18px;border-radius:9px;background:var(--navy);color:var(--white);font-weight:700;font-size:13px;line-height:18px;text-align:center;letter-spacing:1.6px;white-space:nowrap}
  .motto span{color:var(--yellow)}

  /* AI poster */
  .rule{position:absolute;left:98px;width:371px;background:var(--pale);border:1.5px solid var(--navy);border-radius:8px}
  .rule--must{top:150px;height:150px}
  .rule--help{top:308px;height:150px}
  .rule--mustnot{top:467px;height:166px}
  .rule-list{position:absolute;left:97px;right:14px;top:6px;bottom:6px;border-left:2px dotted var(--yellow);list-style:none;display:flex;flex-direction:column}
  .rule-list li{flex:1;display:flex;align-items:center;font-size:13px;line-height:16px;padding:0 0 0 22px;border-bottom:1px solid var(--yellow)}
  .rule-list li:last-child{border-bottom:none}
  .rule-text{position:relative}
  .rule-text::before{content:"";position:absolute;left:-12px;top:6px;width:4px;height:4px;border-radius:50%;background:var(--blue)}
  .rule-label{position:absolute;left:13px;width:170px;background:var(--navy);border-radius:5px;color:var(--white);font-weight:700;font-size:12.5px;line-height:15.5px;text-align:center;display:flex;align-items:flex-end;justify-content:center;padding-bottom:9px}
  .rule-label--must{top:209px;height:52px}
  .rule-label--help{top:353px;height:81px}
  .rule-label--mustnot{top:536px;height:52px}
  .badge{position:absolute;left:77px;width:41px;height:41px;border-radius:50%;background:var(--yellow);border:2px solid var(--white)}
  .badge svg{width:100%;height:100%}
  .badge--must{top:188px}
  .badge--help{top:333px}
  .badge--mustnot{top:515px}
  .tagline{position:absolute;left:0;top:647px;width:484px;height:19px;background:var(--yellow);color:var(--blue);font-weight:700;font-size:10px;line-height:19px;text-align:center;letter-spacing:.4px;white-space:nowrap}
</style>
</head>
<body>

<section class="poster poster--steps">
  <svg class="header-bg" viewBox="0 0 484 150" aria-hidden="true">
    <path d="M0 0H484V142Q250 112 0 132Z" fill="var(--navy)"/>
    <path d="M0 132Q250 112 484 142Q250 118 0 142Z" fill="var(--yellow)"/>
  </svg>
  <div class="school-mark"><span class="dot"></span>CORVAL<br>STATE HIGH</div>
  <p class="kicker">BEFORE YOU ASK THE TEACHER.....</p>
  <h1 class="headline">Try these<br>steps first!</h1>

  <div class="step step--think">
    <div class="step-tab"><span class="step-num">1</span>THINK FIRST</div>
    <div class="step-side">
      <svg viewBox="0 0 40 40" aria-hidden="true"><circle cx="20" cy="20" r="19" fill="var(--blue)" stroke="var(--yellow)" stroke-width="1.5"/><circle cx="21" cy="17" r="6" fill="none" stroke="var(--yellow)" stroke-width="1.8"/><circle cx="21" cy="17" r="2" fill="var(--yellow)"/></svg>
      <span>Don’t give up<br>straight away</span>
    </div>
    <ul class="step-list">
      <li>Read the question carefully</li>
      <li>Identify what you already know</li>
      <li>Try a strategy you’ve used before</li>
      <li>Give yourself thinking time</li>
    </ul>
  </div>

  <div class="step step--supports">
    <div class="step-tab"><span class="step-num">2</span>CHECK YOUR SUPPORTS</div>
    <div class="step-side">
      <svg viewBox="0 0 40 40" aria-hidden="true"><circle cx="20" cy="20" r="19" fill="var(--blue)" stroke="var(--yellow)" stroke-width="1.5"/><rect x="14" y="10" width="14" height="19" rx="1.5" fill="none" stroke="var(--yellow)" stroke-width="1.6"/><path d="M17 15h8M17 19h8M17 23h5" stroke="var(--yellow)" stroke-width="1.4"/><circle cx="14" cy="27" r="4" fill="var(--blue)" stroke="var(--yellow)" stroke-width="1.4"/></svg>
      <span>Before asking<br>for help, check:</span>
    </div>
    <ul class="step-list">
      <li>Learning goal and success criteria</li>
      <li>Worked examples</li>
      <li>Class notes</li>
      <li>Classroom displays</li>
      <li>StudyHub resources</li>
      <li>Task sheet and instructions</li>
    </ul>
  </div>

  <div class="step step--ask">
    <div class="step-tab"><span class="step-num">3</span>ASK 3 BEFORE ME</div>
    <div class="step-side">
      <svg viewBox="0 0 40 40" aria-hidden="true"><circle cx="20" cy="20" r="19" fill="var(--blue)" stroke="var(--yellow)" stroke-width="1.5"/><rect x="9" y="11" width="14" height="10" rx="2" fill="none" stroke="var(--yellow)" stroke-width="1.5"/><rect x="17" y="18" width="15" height="11" rx="2" fill="var(--blue)" stroke="var(--yellow)" stroke-width="1.5"/><path d="M20 22h9M20 25h9" stroke="var(--yellow)" stroke-width="1.2"/></svg>
      <span>Ask three sources<br>before asking the<br>teacher:</span>
    </div>
    <ul class="step-list">
      <li>A person (partner or neighbour)</li>
      <li>A place (notes, display, StudyHub)</li>
      <li>A resource (worked example, task sheet)</li>
      <li class="note">Then ask the teacher if you still need help</li>
    </ul>
  </div>

  <p class="motto"><span>WE BELIEVE.</span> WE STRIVE. <span>WE ACHIEVE</span></p>
</section>

<section class="poster poster--ai">
  <svg class="header-bg" viewBox="0 0 484 150" aria-hidden="true">
    <path d="M0 0H484V142Q250 112 0 132Z" fill="var(--navy)"/>
    <path d="M0 132Q250 112 484 142Q250 118 0 142Z" fill="var(--yellow)"/>
  </svg>
  <div class="school-mark"><span class="dot"></span>CORVAL<br>STATE HIGH</div>
  <h1 class="headline">Using AI and other<br>tools <span class="light">responsibly</span></h1>

  <div class="rule rule--must">
    <ul class="rule-list">
      <li><span class="rule-text">Complete your own work</span></li>
      <li><span class="rule-text">Demonstrate your progress (drafts, notes, planning, revisions)</span></li>
      <li><span class="rule-text">Use feedback to improve your work</span></li>
      <li><span class="rule-text">Demonstrate your understanding of the ideas in your submission</span></li>
    </ul>
  </div>
  <div class="rule-label rule-label--must">WHAT YOU MUST DO</div>
  <div class="badge badge--must"><svg viewBox="0 0 41 41" aria-hidden="true"><path d="M10 21l7 7 14-15" fill="none" stroke="var(--blue)" stroke-width="4.5" stroke-linecap="round" stroke-linejoin="round"/></svg></div>

  <div class="rule rule--help">
    <ul class="rule-list">
      <li><span class="rule-text">Brainstorm ideas</span></li>
      <li><span class="rule-text">Check spelling, grammar and clarity</span></li>
      <li><span class="rule-text">Read your work aloud using text-to-speech tools</span></li>
      <li><span class="rule-text">Help identify areas for improvement in a draft</span></li>
    </ul>
  </div>
  <div class="rule-label rule-label--help">WHAT AI CAN HELP YOU<br>DO (WHEN APPROVED<br>BY YOUR TEACHER)</div>
  <div class="badge badge--help"><svg viewBox="0 0 41 41" aria-hidden="true"><path d="M10 21l7 7 14-15" fill="none" stroke="var(--blue)" stroke-width="4.5" stroke-linecap="round" stroke-linejoin="round"/></svg></div>

  <div class="rule rule--mustnot">
    <ul class="rule-list">
      <li><span class="rule-text">Submit AI generated work as your own</span></li>
      <li><span class="rule-text">Copy and paste AI responses without acknowledging or adapting them</span></li>
      <li><span class="rule-text">Use AI tools to complete the whole task for you</span></li>
      <li><span class="rule-text">Submit work that does not demonstrate your understanding</span></li>
    </ul>
  </div>
  <div class="rule-label rule-label--mustnot">WHAT YOU MUST DO</div>
  <div class="badge badge--mustnot"><svg viewBox="0 0 41 41" aria-hidden="true"><path d="M12 12l17 17M29 12L12 29" stroke="var(--blue)" stroke-width="4.5" stroke-linecap="round"/></svg></div>

  <p class="tagline">IF YOU DIDN’T CREATE, DEVELOP AND UNDERSTAND IT, IT ISN’T YOUR WORK.</p>
</section>

</body>
</html>
```